tinyTally Resource Book - 10 maths tasks to do outside

I need a 22 (11 pages back to back) page A6 sized book produced to standard for submission to professional printer. Needs to be as .pdf file showing guide lines and allowances for colour bleed. I have text already written and submitted as attachment in a Word file with margins set to A6 size. The theme of the materials is "Nature Play" so using lots of pictures from nature (Australia preferably) and showing lots of patterns in nature (rocks, leaves, flower petals etc). Some of the tasks refer to specific activities, such as "shadows" and "floating" so would be great to illustrate appropriately. The big emphasis is on learning outside the classroom, getting kids to engage actively with nature. I would like to see the pages as full colour - so not white background. The book itself will be spiral bound along the top edge so a margin of at least 1cm will be required at the top of each page (or the bottom of even numbered pages). Book will be printed on plastic laminated matte paper for outdoor use. Font size needs to be big enough to read. Fonts sizes, alignments and page numbers are all different at the moment and need to be standardised. One photo is included in a page as a sample if you can use it, otherwise disregard. Logo for Wattlebrook Numeracy Guild is also included to have as part of the acknowledgements at the back of the book.

Target Market(s)

Book is for early childhood and preschool teachers.

Industry/Entity Type

Education

Font styles to use
Sans Serif

Requirements
Must have
• Colour and appeal.
Nice to have
• Use of natural colours instead of bright catchy colours but that is your call.
Should not have
• American spelling

```html
<!DOCTYPE html>
<html lang="en-AU">
<head>
<meta charset="utf-8">
<title>tinyTally – Task 5: Shadows</title>
<link rel="stylesheet" href="https://fonts.googleapis.com/css2?family=Noto+Sans:ital,wght@0,700;0,800;1,700;1,800&family=Questrial&display=swap">
<style>
  :root {
    --paper: #ffffff;
    --wall-light: #efe6d6;
    --wall-mid: #ddd0bb;
    --wall-shade: #b9b2ac;
    --ink-blue: #2b3a92;
    --ink-body: #3a3a3a;
    --bullet-red: #c0283a;
    --crop: #333333;
  }
  * { box-sizing: border-box; margin: 0; padding: 0; }
  html, body { width: 892px; height: 1200px; overflow: hidden; background: var(--paper); }
  .sheet { position: relative; width: 892px; height: 1200px; }
  .crop-marks { position: absolute; inset: 0; }
  .page-photo {
    position: absolute; left: 53px; top: 53px; width: 787px; height: 1094px;
    background:
      radial-gradient(ellipse at 70% 30%, rgba(150,145,150,0.35), transparent 55%),
      radial-gradient(ellipse at 15% 70%, rgba(150,145,150,0.25), transparent 50%),
      linear-gradient(160deg, var(--wall-light) 0%, var(--wall-mid) 60%, var(--wall-light) 100%);
  }
  .task-title, .outcome, .lead, .body-text, .task-list { position: absolute; }
  .task-title {
    top: 100px; left: 0; width: 892px; text-align: center;
    font: 800 45px/1 "Noto Sans", sans-serif; color: var(--ink-blue);
    text-shadow: 0 0 3px #fff, 0 0 3px #fff, 0 0 6px #fff;
  }
  .outcome {
    top: 185px; left: 130px; width: 632px; text-align: center;
    font: 700 28px/40px "Noto Sans", sans-serif; color: var(--ink-blue);
    text-shadow: 0 0 3px #fff, 0 0 5px #fff;
  }
  .lead {
    left: 124px; font: italic 800 22px/30px "Noto Sans", sans-serif; color: var(--ink-blue);
    text-shadow: 0 0 3px #fff, 0 0 5px #fff; letter-spacing: -0.3px;
  }
  .body-text {
    left: 194px; font: 31px/45px "Questrial", sans-serif; color: var(--ink-body);
  }
  .task-list { left: 200px; top: 746px; list-style: none; font: 31px/42px "Questrial", sans-serif; color: var(--ink-body); }
  .task-list li { position: relative; padding-left: 24px; margin-bottom: 4px; }
  .task-list li::before {
    content: ""; position: absolute; left: 0; top: 13px; width: 14px; height: 14px;
    background: var(--bullet-red); transform: rotate(45deg);
  }
  .page-number { position: absolute; left: 692px; top: 995px; width: 60px; height: 58px; }
</style>
</head>
<body>
<div class="sheet">
  <svg class="crop-marks" width="892" height="1200" aria-hidden="true">
    <g stroke="var(--crop)" stroke-width="1" fill="none">
      <path d="M53 0V35M0 53H35M72 0V35M0 72H35"/>
      <path d="M840 0V35M892 53H857M820 0V35M892 72H857"/>
      <path d="M53 1200V1165M0 1147H35M72 1200V1165M0 1128H35"/>
      <path d="M840 1200V1165M892 1147H857M820 1200V1165M892 1128H857"/>
    </g>
  </svg>

  <div class="page-photo" role="img" aria-label="Photograph of bare tree branch shadows cast across a pale sandstone wall with a bed of river pebbles"></div>

  <h1 class="task-title">5. Shadows</h1>
  <h2 class="outcome">EYLF – Outcome 2: Children are connected with and contribute to their world</h2>

  <p class="lead" style="top:329px">Children become socially responsible and show<br>respect for the environment when they...</p>
  <p class="body-text" style="top:398px">demonstrate an increasing<br>knowledge of, and respect<br>for, natural and constructed<br>environments</p>

  <p class="lead" style="top:582px">Educators promote this learning when they...</p>
  <p class="body-text" style="top:618px">model respect, care and appreciation<br>for the natural environment</p>

  <p class="lead" style="top:637px;top:638px">&nbsp;</p>
  <p class="lead" style="top:700px">This task provides an opportunity to:</p>
  <ul class="task-list">
    <li>explore the concepts of<br>”light” and ”shadow”</li>
    <li>record and describe changes<br>to shadows over time</li>
    <li>develop awareness<br>of natural phenomena</li>
  </ul>

  <svg class="page-number" viewBox="0 0 60 58" aria-label="Page 10">
    <polygon points="30,1 59,22 48,57 12,57 1,22" fill="var(--ink-blue)"/>
    <text x="30" y="41" text-anchor="middle" fill="#fff" font-family="Questrial, sans-serif" font-size="26">10</text>
  </svg>
</div>
</body>
</html>
```